Banner for promote service of debit card

We are PagoLume and we need the banners to be posted on the facebook and instagram pages.
We want something to communicate that it is an exclusive debit card full of services.
Low commissions.
Our competitors:
https://www.kelmora.example/it/home.html
https://www.zofe.example/it/
https://www.socialpage.example/ostrevabank/
monadrift
maybe some banner that makes the idea of a convenient debit card that everyone can use.
Girls enjoying card shopping.
Please check also website for slogans and phrases to use
https://www.pagolume.example/
Should show the services.
We must convey that it is a fast, simple card that guarantees privacy.
We need strong banners that attract people as these ban will be sponsored on instagram and facebook
People 18-35 y
Open Bank account. low commissions. Easy to use. No limits. 100% Privacy.
- Written in Italian.

```html
<!DOCTYPE html>
<html lang="it">
<head>
<meta charset="utf-8">
<title>PagoLume – Una carta per tutti</title>
<link href="https://fonts.googleapis.com/css2?family=Montserrat:wght@600;700&family=Roboto:wght@400;500&display=swap" rel="stylesheet">
<style>
  :root {
    --photo-dark: #3a1d0c;
    --photo-mid: #9a5a2c;
    --photo-light: #e3a56a;
    --headline-band: rgba(70, 36, 16, 0.72);
    --text-white: #ffffff;
    --brand-grey: #d9d2cc;
    --brand-dot: #e8422f;
    --card-black: #151515;
    --card-edge: #2b2b2b;
    --card-gold: #e9c45a;
    --chip-gold: #c9a14a;
  }
  * { margin: 0; padding: 0; box-sizing: border-box; }
  html, body { width: 1200px; height: 900px; overflow: hidden; }
  body { font-family: "Montserrat", sans-serif; background: var(--photo-dark); }

  .banner { position: relative; width: 1200px; height: 900px; overflow: hidden; }

  .banner-photo {
    position: absolute; inset: 0;
    background:
      radial-gradient(ellipse at 62% 55%, rgba(40,20,8,0.75) 0%, rgba(40,20,8,0) 45%),
      radial-gradient(ellipse at 85% 40%, var(--photo-light) 0%, rgba(227,165,106,0) 55%),
      linear-gradient(100deg, var(--photo-mid) 0%, var(--photo-light) 45%, var(--photo-mid) 75%, var(--photo-dark) 100%);
  }

  .headline-band {
    position: absolute; left: 0; top: 48px;
    width: 955px; height: 252px;
    background: var(--headline-band);
    padding: 22px 0 0 66px;
  }
  .headline {
    color: var(--text-white);
    font-weight: 700; font-size: 82px; line-height: 1.12;
    letter-spacing: 0.5px;
  }

  .tagline {
    position: absolute; left: 76px; top: 365px;
    color: var(--text-white);
    font-weight: 700; font-size: 40px; line-height: 1.45;
    text-shadow: 0 2px 6px rgba(0,0,0,0.45);
  }

  .brand {
    position: absolute; left: 76px; top: 770px;
    display: flex; align-items: center; gap: 18px;
  }
  .brand-dot { width: 46px; height: 46px; border-radius: 50%; background: var(--brand-dot); }
  .brand-name { color: var(--brand-grey); font-weight: 700; font-size: 38px; }

  .debit-card {
    position: absolute; left: 776px; top: 612px;
    width: 360px; height: 228px;
    border-radius: 16px;
    background: linear-gradient(135deg, var(--card-edge) 0%, var(--card-black) 60%);
    box-shadow: 0 8px 20px rgba(0,0,0,0.5);
    font-family: "Roboto", sans-serif;
    color: var(--card-gold);
  }
  .card-brand {
    position: absolute; left: 22px; top: 18px;
    font-family: "Montserrat", sans-serif; font-weight: 700; font-size: 20px;
    color: var(--card-gold);
  }
  .card-tier { position: absolute; right: 26px; top: 14px; text-align: center; }
  .card-tier-label { font-size: 24px; font-weight: 500; }
  .card-tier-issuer { font-family: "Montserrat", sans-serif; font-size: 13px; font-weight: 600; }
  .card-chip { position: absolute; left: 40px; top: 78px; }
  .card-number {
    position: absolute; left: 40px; top: 120px;
    font-size: 25px; letter-spacing: 2px; word-spacing: 10px;
  }
  .card-expiry { position: absolute; left: 150px; top: 156px; font-size: 8px; color: #bba36a; }
  .card-holder { position: absolute; left: 26px; bottom: 22px; font-size: 12px; color: #d8d0c0; }
  .card-network {
    position: absolute; right: 22px; bottom: 18px;
    font-family: "Montserrat", sans-serif; font-size: 15px; font-weight: 700; color: var(--card-gold);
  }
</style>
</head>
<body>
  <main class="banner">
    <div class="banner-photo" role="img" aria-label="Fotografia: ragazza bionda di spalle con le braccia alzate in una strada cittadina illuminata di sera, toni caldi arancioni"></div>

    <div class="headline-band">
      <h1 class="headline">All in One !<br>Una carta per tutti</h1>
    </div>

    <p class="tagline">
      Enjoy your cart!<br>
      Fai quello che vuoi,<br>
      Nessun limite.<br>
      Nessun controllo.
    </p>

    <div class="brand">
      <span class="brand-dot"></span>
      <span class="brand-name">PagoLume</span>
    </div>

    <div class="debit-card">
      <span class="card-brand">PagoLume</span>
      <div class="card-tier">
        <div class="card-tier-label">Business</div>
        <div class="card-tier-issuer">PagoLume</div>
      </div>
      <svg class="card-chip" width="40" height="32" viewBox="0 0 40 32">
        <rect x="0.5" y="0.5" width="39" height="31" rx="5" fill="var(--chip-gold)" stroke="#8a6c2c"/>
        <path d="M0 11h13M0 21h13M27 11h13M27 21h13M13 0v32M27 0v32M13 16h14" stroke="#8a6c2c" stroke-width="1.2" fill="none"/>
      </svg>
      <div class="card-number">1234 5678 9012 3456</div>
      <div class="card-expiry">VALID 09/25</div>
      <div class="card-holder">MARCO RIVA</div>
      <div class="card-network">Trevona</div>
    </div>
  </main>
</body>
</html>
```